New Dental Office Needs an Attractive and user friendly Website Designed

I need a website for a new dental office. The Name is Harrowfield Dentistry. I would like a Modern design with a user friendly interface and usability.
I would like a landing page, a page that lists the services we offer: Cosmetic Dentistry, Implants, Dental Hygiene, Emergency Services, Restorations, Dentures
Target Market(s)
Mid to upper class
Industry/Entity Type
Dentistry
Coding
Number of Pages Required
1 page
Requirements
Must have
- Landing page that has a scheduling option, Procedures, operating hours, and contact us info
Nice to have
- Appealing design, Soft comforting colors. Easy to navigate page, Modern and professional.

```html
<!DOCTYPE html>
<html lang="en">
<head>
<meta charset="utf-8">
<title>Harrowfield Dentistry</title>
<link href="https://fonts.googleapis.com/css2?family=Spectral:wght@500;600&family=Lato:wght@400;700&display=swap" rel="stylesheet">
<style>
:root{
  --navy:#0b3446;
  --navy-soft:#0f4a57;
  --mist:#d8dee0;
  --cream:#efede9;
  --ink:#1d2a30;
  --white:#ffffff;
  --mint:#3fd1b0;
  --line:#cfe3d6;
}
*{box-sizing:border-box;margin:0;padding:0}
html,body{width:1200px;height:5164px;overflow:hidden}
body{font-family:'Lato',sans-serif;color:var(--ink);background:var(--white);position:relative}
.serif{font-family:'Spectral',serif}
.abs{position:absolute}
.btn{position:absolute;display:flex;align-items:center;justify-content:center;background:var(--navy);color:var(--white);font-size:20px;border-radius:3px}
h1,h2,h3{font-family:'Spectral',serif;font-weight:500;color:var(--navy);letter-spacing:2px}

.topbar{top:0;left:0;width:1200px;height:40px;background:var(--navy)}
.topbar .phone{left:92px;top:10px;color:var(--white);font-size:15px;display:flex;align-items:center;gap:8px}
.topbar .social{right:92px;top:11px;display:flex;gap:10px}
.topbar .social span{width:17px;height:17px;border-radius:3px;background:var(--white);display:block}

.nav{top:40px;left:0;width:1200px;height:96px;border-bottom:2px solid var(--line);background:var(--white)}
.brand{position:absolute;font-family:'Spectral',serif;font-weight:600;color:var(--navy);font-size:30px;letter-spacing:0}
.nav .brand{left:96px;top:26px}
.nav .links{left:551px;top:37px;display:flex;gap:0;font-size:17px;color:var(--navy)}
.nav .links a{position:absolute;white-space:nowrap;color:var(--navy);text-decoration:none}

.hero{top:136px;left:0;width:1200px;height:530px;background:var(--cream)}
.hero h1{position:absolute;left:88px;top:96px;font-size:56px;line-height:68px;font-weight:600}
.hero p{position:absolute;left:88px;top:252px;font-size:27px;line-height:44px;color:var(--ink)}
.hero-photo{position:absolute;left:600px;top:0;width:600px;height:530px;background:linear-gradient(100deg,#ece8e2 0%,#d9c8b8 40%,#5f4a3e 70%,#1f2a44 100%)}

.about{top:666px;left:0;width:1200px;height:268px;background:var(--mist)}
.leaf-field{position:absolute;background:#c9d3d6;border-radius:40px}
.about h2{position:absolute;left:86px;top:96px;font-size:50px}
.about p{position:absolute;left:342px;top:92px;font-size:24px;line-height:32px;width:780px}

.services h2{position:absolute;left:0;width:1200px;text-align:center;top:1024px;font-size:50px}
.services .sub{position:absolute;left:0;width:1200px;text-align:center;top:1102px;font-size:24px}
.svc{position:absolute;width:340px;text-align:center}
.svc svg{display:block;margin:0 auto;width:80px;height:80px}
.svc h3{font-family:'Lato',sans-serif;font-weight:700;font-size:23px;letter-spacing:0;margin-top:32px;color:var(--navy)}
.svc p{font-size:16px;line-height:24px;margin-top:8px}
.svc .btn{position:relative;width:158px;height:50px;margin:30px auto 0}

.cta{top:1950px;left:0;width:1200px;height:384px;background:var(--navy);overflow:hidden}
.cta .leaf{position:absolute;right:-20px;top:-40px;width:420px;height:420px;background:var(--navy-soft);border-radius:50% 50% 50% 0;opacity:.8}
.cta h2{position:absolute;left:88px;top:80px;font-size:50px;color:var(--white);font-weight:600}
.cta p{position:absolute;left:88px;top:158px;font-size:24px;line-height:34px;color:var(--white)}
.cta .btn{left:88px;top:256px;width:156px;height:46px;background:var(--white);color:var(--navy)}

.hours h2{position:absolute;left:88px;top:2426px;font-size:50px;line-height:68px}
.hours-box{position:absolute;left:88px;top:2612px;width:468px;height:378px;background:var(--mist);border-radius:16px;padding:42px 0 0 32px;font-size:24px}
.hours-box .row{display:flex;height:42.5px}
.hours-box .day{width:182px}
.address{left:106px;top:3034px;font-size:24px;line-height:32px}
.hours .btn{left:106px;top:3118px;width:190px;height:50px}
.room-photo{position:absolute;left:616px;top:2426px;width:496px;height:734px;background:linear-gradient(180deg,#ece6da 0%,#e6dccb 70%,#d5c3a6 100%)}

.reviews{top:3284px;left:0;width:1200px;height:582px;background:var(--mist)}
.reviews h2{position:absolute;left:0;width:1200px;text-align:center;top:100px;font-size:50px}
.card{position:absolute;top:214px;width:320px;height:272px;background:var(--white);border-radius:10px;padding:34px 46px;font-size:19px;line-height:34px;color:var(--ink)}
.card .q{color:var(--mint);font-family:'Spectral',serif;font-size:64px;line-height:40px;font-weight:600;height:40px}
.card .who{margin-top:22px;font-weight:700}

.book{top:3866px;left:0;width:1200px;height:554px;background:var(--white)}
.book h2{position:absolute;left:88px;top:114px;font-size:50px;line-height:68px}
.book p{position:absolute;left:88px;top:284px;font-size:24px;line-height:36px}
.book .btn{left:88px;top:392px;width:190px;height:50px}
.book-photo{position:absolute;left:630px;top:0;width:570px;height:554px;background:linear-gradient(90deg,#f3efe8 0%,#6f9098 30%,#8a9aa0 55%,#b9aea4 100%)}

.news{top:4420px;left:0;width:1200px;height:380px;background:var(--mist)}
.news h2{position:absolute;left:0;width:1200px;text-align:center;top:70px;font-size:50px}
.news p{position:absolute;left:0;width:1200px;text-align:center;top:162px;font-size:24px}
.news .field{position:absolute;left:306px;top:242px;width:394px;height:56px;background:var(--white);font-size:20px;padding:17px 0 0 38px;color:var(--ink)}
.news .btn{left:700px;top:242px;width:194px;height:56px;font-size:28px}

.foot{top:4800px;left:0;width:1200px;height:364px;background:var(--white);overflow:hidden}
.foot .brand{left:0;width:1200px;text-align:center;top:62px}
.foot .links{position:absolute;left:0;width:1200px;top:152px;text-align:center;font-size:18px;word-spacing:0}
.foot .links span{margin:0 19px}
.foot .legal{position:absolute;left:0;width:1200px;top:208px;text-align:center;font-size:18px}
.foot .copy{position:absolute;left:0;width:1200px;top:264px;text-align:center;font-size:18px}
</style>
</head>
<body>

<div class="abs topbar">
  <div class="abs phone">
    <svg width="11" height="17" viewBox="0 0 11 17"><rect x="0.5" y="0.5" width="10" height="16" rx="2" fill="#fff"/></svg>
    (555) 014-2290
  </div>
  <div class="abs social" aria-label="Social links"><span></span><span></span><span></span></div>
</div>

<header class="abs nav">
  <div class="brand">Harrowfield Dentistry</div>
  <nav class="abs links">
    <a style="left:0">Services</a>
    <a style="left:135px">About</a>
    <a style="left:244px">Contact</a>
  </nav>
  <div class="btn" style="left:946px;top:22px;width:168px;height:50px;font-size:21px">Book Online</div>
</header>

<section class="abs hero">
  <h1>Advance Care with<br>a Gentle Touch</h1>
  <p>Advanced Care with a Gentle Touch.<br>Because Your Smile Deserves the Best.</p>
  <div class="btn" style="left:86px;top:358px;width:268px;height:50px">Schedule Appointment</div>
  <div class="hero-photo" role="img" aria-label="Smiling family of a mother, young son and father"></div>
</section>

<section class="abs about">
  <div class="leaf-field" style="left:0;top:0;width:210px;height:268px" role="img" aria-label="Soft leaf pattern decoration"></div>
  <div class="leaf-field" style="left:980px;top:0;width:220px;height:268px" role="img" aria-label="Soft leaf pattern decoration"></div>
  <h2>About Us</h2>
  <p>Providing exceptional dental care in a tranquil, spa-like setting. We cater to your individual needs with state-of-the-art technology and a gentle personal approach.</p>
</section>

<section class="services">
  <h2>Our Services</h2>
  <div class="sub">Comprehensive Dental Solutions, Tailored to You.</div>

  <div class="svc" style="left:82px;top:1214px">
    <svg viewBox="0 0 80 80" fill="none" stroke="#0b3446" stroke-width="3" stroke-linejoin="round"><path d="M14 18c0-10 12-12 18-8 4 3 8 3 12 0 6-4 16-2 16 8 0 10-4 16-6 26-2 12-2 24-8 24-5 0-5-18-10-18s-5 18-10 18c-6 0-6-12-8-24-2-10-4-16-4-26z"/><path d="M64 4l3 7 7 3-7 3-3 7-3-7-7-3 7-3z"/></svg>
    <h3>Cosmetic Dentistry</h3>
    <p>Whitening, veneers, and smile<br>makeovers for a confident appearance.</p>
    <div class="btn">Learn More</div>
  </div>
  <div class="svc" style="left:430px;top:1214px">
    <svg viewBox="0 0 80 80" fill="none" stroke="#0b3446" stroke-width="3" stroke-linejoin="round"><path d="M24 6c8-4 24-4 32 0 4 2 4 14 0 18H24c-4-4-4-16 0-18z"/><path d="M26 30h28M28 38h24M30 46h20M32 54h16M34 62h12"/><path d="M36 70l4 6 4-6"/></svg>
    <h3>Dental Implants</h3>
    <p>Permanent tooth replacement<br>with natural look, feel, and function.</p>
    <div class="btn">Learn More</div>
  </div>
  <div class="svc" style="left:778px;top:1214px">
    <svg viewBox="0 0 80 80" fill="none" stroke="#0b3446" stroke-width="3" stroke-linejoin="round"><path d="M6 70l40-36 6 6-40 36z"/><path d="M40 40l-6-6M36 44l-6-6"/><path d="M64 8c4 6 8 10 8 14a8 8 0 01-16 0c0-4 4-8 8-14z"/></svg>
    <h3>Hygiene &amp; Cleanings</h3>
    <p>Thorough, professional cleanings<br>to protect your oral health.</p>
    <div class="btn">Learn More</div>
  </div>

  <div class="svc" style="left:82px;top:1576px">
    <svg viewBox="0 0 80 80" fill="none" stroke="#0b3446" stroke-width="3" stroke-linejoin="round"><path d="M40 6l28 10v22c0 18-12 30-28 36C24 68 12 56 12 38V16z"/><path d="M34 26h12v8h8v12h-8v8H34v-8h-8V34h8z"/></svg>
    <h3>Emergency Services</h3>
    <p>Prompt, compassionate care<br>when dental issues can't wait.</p>
    <div class="btn">Learn More</div>
  </div>
  <div class="svc" style="left:430px;top:1576px">
    <svg viewBox="0 0 80 80" fill="none" stroke="#0b3446" stroke-width="3" stroke-linejoin="round"><path d="M14 18c0-10 12-12 18-8 4 3 8 3 12 0 6-4 16-2 16 8 0 10-4 16-6 26-2 12-2 24-8 24-5 0-5-18-10-18s-5 18-10 18c-6 0-6-12-8-24-2-10-4-16-4-26z"/><path d="M24 20c4-4 10-2 14 0"/></svg>
    <h3>Restorations</h3>
    <p>Repair and strengthen teeth<br>with expertly crafted solutions.</p>
    <div class="btn">Learn More</div>
  </div>
  <div class="svc" style="left:778px;top:1576px">
    <svg viewBox="0 0 80 80" fill="none" stroke="#0b3446" stroke-width="3" stroke-linejoin="round"><path d="M4 30c10 6 62 6 72 0-2 14-14 22-36 22S6 44 4 30z"/><path d="M16 34v8M26 36v10M36 36v12M46 36v12M56 36v10M66 34v8"/></svg>
    <h3>Dentures &amp; Partials</h3>
    <p>Custom full or partial dentures<br>designed for comfort and fit.</p>
    <div class="btn">Learn More</div>
  </div>
</section>

<section class="abs cta">
  <div class="leaf" role="img" aria-label="Large soft leaf shape"></div>
  <h2>Time to Prioritize Yourself.</h2>
  <p>Book your appointment with Harrowfield Dentistry and experience<br>our calming environment and personalized attention first hand.</p>
  <div class="btn">Learn More</div>
</section>

<section class="hours">
  <h2>Office Hours<br>&amp; Location</h2>
  <div class="hours-box">
    <div class="row"><span class="day">Monday</span><span>8:00 AM - 4:30 PM</span></div>
    <div class="row"><span class="day">Tuesday</span><span>8:00 AM - 4:30 PM</span></div>
    <div class="row"><span class="day">Wednesday</span><span>Closed</span></div>
    <div class="row"><span class="day">Thursday</span><span>8:00 AM - 4:30 PM</span></div>
    <div class="row"><span class="day">Friday</span><span>8:00 AM - 4:30 PM</span></div>
    <div class="row"><span class="day">Saturday</span><span>Closed</span></div>
    <div class="row"><span class="day">Sunday</span><span>Closed</span></div>
  </div>
  <div class="abs address">418 Wrenfield Avenue Ste 107<br>Alder Falls, TN 37790</div>
  <div class="btn">Get Directions</div>
  <div class="room-photo" role="img" aria-label="Calm waiting room with a cream armchair and a potted fiddle-leaf plant"></div>
</section>

<section class="abs reviews">
  <h2>What Our Patients Are Saying</h2>
  <div class="card" style="left:88px;text-align:center">
    <div class="q" style="text-align:left">&ldquo;</div>
    The staff is very friendly<br>and professional. Highly<br>recommend this office!
    <div class="who" style="text-align:left">- Nora K</div>
  </div>
  <div class="card" style="left:440px">
    <div class="q">&ldquo;</div>
    My experience with the<br>Doctor was fantastic.<br>I feel confident in my smile.
    <div class="who">- Caleb M</div>
  </div>
  <div class="card" style="left:792px;color:#3d6a78">
    <div class="q">&ldquo;</div>
    I had an emergency and<br>Got same-day treatment.<br>So grateful for the care!
    <div class="who">- Priya R</div>
  </div>
</section>

<section class="abs book">
  <div class="leaf-field" style="left:320px;top:0;width:310px;height:250px;background:#e6ebec" role="img" aria-label="Soft leaf pattern decoration"></div>
  <h2>Book an<br>Appointment</h2>
  <p>Ready for a healthier smile?<br>Scheduling your visit is quick and easy.</p>
  <div class="btn">Schedule Now</div>
  <div class="book-photo" role="img" aria-label="Smiling couple standing side by side"></div>
</section>

<section class="abs news">
  <h2>Subscribe to Our Newsletter</h2>
  <p>Stay up to date with our latest news and dental tips.</p>
  <div class="field">Enter your email address</div>
  <div class="btn">Subscribe</div>
</section>

<footer class="abs foot">
  <div class="leaf-field" style="left:-20px;top:0;width:260px;height:364px;background:#e3e9ea" role="img" aria-label="Soft leaf pattern decoration"></div>
  <div class="leaf-field" style="left:950px;top:0;width:270px;height:364px;background:#e3e9ea" role="img" aria-label="Soft leaf pattern decoration"></div>
  <div class="brand">Harrowfield Dentistry</div>
  <div class="links"><span>Home</span><span>Services</span><span>About</span><span>Contact</span></div>
  <div class="legal">Privacy Policy | Terms</div>
  <div class="copy">© 2025 Harrowfield Dentistry. All rights reserved.</div>
</footer>

</body>
</html>
```